Flyer for the Lumen 2025 Conference

I am looking to produce a flyer for our upcoming conference, Lumen 2025. This is an annual conference that we plan to publicize on social media. The ideal designer will create a flyer that is eye-catching and effectively communicates the key information. Please see attached our logo, speaker photo, and flyer content.

Target Market(s)

All demographics

Industry/Entity Type

Christian

Font styles to use
Sans Serif

Requirements
Should not have
• Cross, church

```html
<!DOCTYPE html>
<html lang="en">
<head>
<meta charset="utf-8">
<title>Lumen 2025 Conference Flyer</title>
<link href="https://fonts.googleapis.com/css2?family=Antonio:wght@300;400;500;700&family=Saira:wght@300;400&display=swap" rel="stylesheet">
<style>
  :root {
    --stage: #d3d3d3;
    --navy-deep: #0d1a30;
    --navy: #1a2c4a;
    --storm: #33445e;
    --white: #ffffff;
    --orange: #f39a2b;
    --pill-blue: #4a55c9;
    --live-red: #e8252a;
  }
  * { margin: 0; padding: 0; box-sizing: border-box; }
  html, body { width: 1044px; height: 1200px; overflow: hidden; }
  body { background: var(--stage); position: relative; font-family: "Antonio", sans-serif; color: var(--white); }
  .flyer {
    position: absolute; left: 0; top: 78px; width: 1044px; height: 1044px; overflow: hidden;
    background: radial-gradient(ellipse at 35% 30%, var(--storm) 0%, var(--navy) 45%, var(--navy-deep) 100%);
  }
  .abs { position: absolute; }
  .speaker-photo {
    left: 467px; top: 126px; width: 577px; height: 918px;
    background: linear-gradient(160deg, rgba(31,95,180,0) 0%, rgba(31,95,180,0.55) 35%, rgba(20,70,150,0.8) 70%, rgba(13,26,48,0.3) 100%);
    border-radius: 260px 260px 0 0;
  }
  .live-pill {
    left: 835px; top: 19px; width: 178px; height: 49px; border-radius: 25px; background: var(--pill-blue);
    display: flex; align-items: center; justify-content: center; gap: 12px;
  }
  .live-pill .label { font-weight: 700; font-size: 17px; line-height: 18px; text-align: center; letter-spacing: 0.5px; }
  .live-pill .label span { display: block; }
  .live-pill .dot { width: 28px; height: 28px; border-radius: 50%; background: var(--live-red); }
  .title { left: 33px; top: 57px; font-weight: 400; font-size: 217px; line-height: 217px; letter-spacing: 1px; white-space: nowrap; }
  .year {
    left: 538px; top: 94px; width: 66px; height: 183px;
    writing-mode: vertical-rl; transform: rotate(180deg);
    font-weight: 300; font-size: 74px; line-height: 66px; letter-spacing: 12px; text-align: center;
  }
  .subtitle { left: 42px; top: 298px; font-size: 47px; line-height: 47px; font-weight: 400; letter-spacing: 6.5px; white-space: nowrap; }
  .topic { left: 45px; top: 415px; width: 438px; }
  .topic .head { display: flex; align-items: center; gap: 8px; font-family: "Saira", sans-serif; font-size: 19px; line-height: 22px; letter-spacing: 1px; }
  .topic .head::before, .topic .head::after { content: ""; flex: 1; height: 1px; background: var(--white); }
  .topic .theme { font-family: "Saira", sans-serif; font-weight: 300; font-size: 38px; line-height: 44px; text-align: center; letter-spacing: 1px; border-bottom: 1px solid var(--white); padding-bottom: 4px; }
  .section-label { font-family: "Saira", sans-serif; color: var(--orange); font-size: 16px; line-height: 20px; letter-spacing: 1.5px; text-align: center; width: 200px; left: 160px; }
  .dates { left: 43px; top: 574px; width: 434px; display: flex; }
  .day { flex: 1; text-align: center; border-left: 1px solid var(--white); height: 77px; padding-top: 6px; }
  .day:first-child { border-left: none; }
  .day .name { font-size: 15px; line-height: 20px; }
  .day .date { font-size: 22px; line-height: 24px; color: var(--orange); font-weight: 500; }
  .day .time { font-size: 15px; line-height: 20px; }
  .address { left: 60px; top: 707px; width: 400px; text-align: center; font-weight: 300; font-size: 18px; line-height: 22px; }
  .more { left: 160px; top: 788px; width: 200px; text-align: center; font-family: "Saira", sans-serif; font-size: 12px; line-height: 14px; letter-spacing: 3px; text-decoration: underline; }
  .download { left: 30px; top: 811px; width: 460px; text-align: center; font-weight: 300; font-size: 18px; line-height: 22px; }
  .store-badge { top: 844px; width: 142px; height: 39px; border-radius: 5px; background: #000; border: 1px solid #888; }
  .contacts { left: 67px; top: 908px; list-style: none; }
  .contacts li { display: flex; align-items: center; gap: 8px; font-weight: 700; font-size: 19px; height: 32px; }
  .contacts svg { width: 18px; height: 18px; }
  .brand { left: 300px; top: 930px; display: flex; align-items: center; gap: 10px; }
  .brand .mark { width: 20px; height: 20px; border-radius: 50%; background: var(--orange); }
  .brand .name { font-size: 50px; line-height: 56px; font-weight: 400; letter-spacing: 3px; }
  .speaker { left: 753px; top: 782px; width: 280px; }
  .speaker .role { padding-left: 28px; font-family: "Saira", sans-serif; font-weight: 300; font-size: 27px; letter-spacing: 4px; line-height: 32px; border-bottom: 1px solid rgba(255,255,255,0.6); width: 166px; padding-bottom: 2px; }
  .speaker .names { padding-left: 28px; margin-top: 4px; font-size: 60px; line-height: 60px; font-weight: 400; letter-spacing: 5px; }
</style>
</head>
<body>
  <main class="flyer">
    <div class="abs speaker-photo" role="img" aria-label="Portrait of the speaker in a blue suit and glasses against a stormy sky"></div>

    <div class="abs live-pill">
      <div class="label"><span>LIVE</span><span>STREAMING</span></div>
      <div class="dot"></div>
    </div>

    <h1 class="abs title">LUMEN</h1>
    <div class="abs year">2025</div>
    <h2 class="abs subtitle">A PROPHETIC CONFERENCE</h2>

    <section class="abs topic">
      <div class="head">TOPIC</div>
      <div class="theme">The Voice Of The Lord</div>
    </section>

    <div class="abs section-label" style="top:532px">DATE / TIME</div>
    <section class="abs dates">
      <div class="day"><div class="name">FRIDAY</div><div class="date">DECEMBER 26TH</div><div class="time">6:30PM - 9:00PM</div></div>
      <div class="day"><div class="name">SATURDAY</div><div class="date">DECEMBER 27TH</div><div class="time">5:30PM - 8:00PM</div></div>
      <div class="day"><div class="name">SUNDAY</div><div class="date">DECEMBER 29TH</div><div class="time">4:30PM - 7:00PM</div></div>
    </section>

    <div class="abs section-label" style="top:677px">LOCATION</div>
    <p class="abs address">The Harbor Hill Performing Arts Center<br>218 Linden Street Fairhaven, Maine 04011</p>

    <div class="abs more">MORE INFO</div>
    <p class="abs download">Download the KAVOR App to stay updated on the event</p>
    <div class="abs store-badge" style="left:112px"></div>
    <div class="abs store-badge" style="left:266px"></div>

    <ul class="abs contacts">
      <li><svg viewBox="0 0 24 24" fill="none" stroke="#fff" stroke-width="2"><path d="M5 3h4l2 5-3 2a12 12 0 0 0 6 6l2-3 5 2v4a2 2 0 0 1-2 2A17 17 0 0 1 3 5a2 2 0 0 1 2-2z"/></svg>555 014 2290</li>
      <li><svg viewBox="0 0 24 24" fill="none" stroke="#fff" stroke-width="2"><rect x="2" y="5" width="20" height="14" rx="1"/><path d="M2 6l10 7 10-7"/></svg>hello@kavor.org</li>
      <li><svg viewBox="0 0 24 24" fill="none" stroke="#fff" stroke-width="2"><circle cx="12" cy="12" r="10"/><path d="M2 12h20M12 2c3 3 3 17 0 20M12 2c-3 3-3 17 0 20"/></svg>www.kavor.org</li>
    </ul>

    <div class="abs brand"><div class="mark"></div><div class="name">KAVOR</div></div>

    <section class="abs speaker">
      <div class="role">SPEAKER</div>
      <div class="names">PROPHET<br>ELIAS<br>MARLOW</div>
    </section>
  </main>
</body>
</html>
```